Client Meeting and installation Email Follow up

I would like a follow-up email template created.
Currently, we do a lot of new construction builds and meet with clients about 6-3 months before they take possession of their new house. I want a follow-up email template to be sent after the homeowner takes possession of their house that enquires if the clients are happy about their new lighting, the service they received, and their customer service representative with Brightwell Lamps and Breezes. I have attached a few files of what our current marketing looks like.
Target Market(s)
Home Owners We have already met with
Industry/Entity Type
Residential lighting
Font styles to use
Other font styles liked:
- Alta Light, Playfair Display, Montserrat
Colors
Designer to choose colors to be used in the design.
Look and feel
Each slider illustrates characteristics of the customer's brand and the style your logo design should communicate.

```html
<!DOCTYPE html>
<html lang="en">
<head>
<meta charset="utf-8">
<title>Brightwell Lamps and Breezes – Lighting Follow-up</title>
<link rel="stylesheet" href="https://fonts.googleapis.com/css2?family=Josefin+Sans:wght@300;400&family=Montserrat:wght@400;600&family=Playfair+Display&display=swap">
<style>
:root{
  --page:#dcc6c6;
  --beige:#ecdfd7;
  --brown:#9b7f6d;
  --grey:#f1f1f1;
  --dark:#262626;
  --ink:#222;
  --rule:#9b7f6d;
  --light-beige:#efdccf;
}
*{margin:0;padding:0;box-sizing:border-box}
html,body{width:1200px;height:4286px;overflow:hidden}
body{background:var(--page);position:relative;font-family:"Montserrat",sans-serif;color:var(--ink)}
.email{position:absolute;left:192px;top:160px;width:816px;height:3964px;background:#fff;overflow:hidden;box-shadow:0 20px 50px rgba(80,50,50,.25)}
.abs{position:absolute}
.header-shape{left:0;top:0}
.logo{left:220px;top:67px;width:376px;height:109px;background:#fff;display:flex;align-items:center;justify-content:center;text-align:center;font-family:"Josefin Sans",sans-serif;font-weight:400;font-size:29px;line-height:1.15;letter-spacing:1px;color:#111}
.rule{height:2px;background:var(--rule)}
.photo{border-radius:12px}
.hero-photo{left:133px;top:303px;width:561px;height:459px;background:linear-gradient(160deg,#e9d6d3 0%,#cfc7c9 45%,#a9a4a8 100%)}
.title{left:0;width:816px;text-align:center;font-family:"Josefin Sans",sans-serif;font-weight:300;color:var(--ink)}
.title-small{top:845px;font-size:50px;letter-spacing:2px}
.title-big{top:903px;font-size:118px;line-height:1;letter-spacing:2px}
.tag{left:195px;top:1042px;width:441px;height:63px;border:2px solid var(--rule);display:flex;align-items:center;justify-content:center;font-family:"Josefin Sans",sans-serif;font-size:28px;letter-spacing:6px}
.intro{left:120px;width:576px;top:1188px;text-align:center;font-size:24px;line-height:35px}
.band-brown{left:0;top:1330px;width:816px;height:512px;background:var(--brown)}
.band-beige{left:0;top:1842px;width:816px;height:562px;background:var(--beige)}
.band-grey{left:0;top:2404px;width:816px;height:531px;background:var(--grey)}
.band-dark{left:0;top:3498px;width:816px;height:466px;background:var(--dark)}
.lead{left:100px;width:627px;top:1410px;text-align:center;font-size:20px;line-height:27px;color:#fff}
.question{font-family:"Playfair Display",serif;font-size:36px;line-height:46px}
.kitchen-photo{left:75px;top:1576px;width:324px;height:356px;background:linear-gradient(170deg,#f2f0ec 0%,#d9d2c8 45%,#3c3633 70%,#e8e8e6 100%)}
.q1{left:438px;top:1610px;width:340px;color:var(--light-beige)}
.nook-photo{left:434px;top:1972px;width:325px;height:354px;background:linear-gradient(180deg,#f4f3ef 0%,#e4e0d6 50%,#2f4b48 80%,#c9a46a 100%)}
.q2{left:75px;top:2040px;width:320px;color:var(--ink)}
.pendant-photo{left:75px;top:2488px;width:324px;height:354px;background:linear-gradient(150deg,#efeeec 0%,#dddbd7 50%,#c8943f 85%,#4b5a3c 100%)}
.q3{left:438px;top:2530px;width:340px;color:var(--ink)}
.foliage{background:linear-gradient(135deg,rgba(72,110,52,.55),rgba(120,160,90,0))}
.foliage-top{left:0;top:2935px;width:150px;height:225px}
.foliage-bottom{left:740px;top:3299px;width:76px;height:199px;background:linear-gradient(315deg,rgba(72,110,52,.55),rgba(120,160,90,0))}
.commit{left:100px;width:616px;top:3092px;text-align:center;font-weight:600;font-size:30px;line-height:41px}
.help{left:120px;width:576px;top:3274px;text-align:center;font-size:24px;line-height:35px}
.thanks{left:110px;width:596px;top:3580px;text-align:center;font-size:18px;line-height:27px;color:#cfcfcf}
.regards{left:0;width:816px;top:3698px;text-align:center;font-family:"Josefin Sans",sans-serif;font-weight:300;font-size:46px;letter-spacing:2px;color:var(--light-beige)}
.team{left:0;width:816px;top:3754px;text-align:center;font-size:17px;color:#ddd}
.social{top:3819px;width:32px;height:32px;border-radius:50%;background:#f0f0f0}
.rule-dark{left:33px;top:3890px;width:749px;height:1px;background:#4a4a4a}
.site{left:0;width:816px;top:3913px;text-align:center;font-size:17px;color:#ddd}
</style>
</head>
<body>
<main class="email">
  <svg class="abs header-shape" width="816" height="600" viewBox="0 0 816 600" aria-hidden="true">
    <path d="M0 0H816V448C700 470 610 455 520 470C400 490 300 600 120 560C70 548 30 530 0 510Z" fill="var(--beige)"/>
  </svg>
  <div class="abs logo">BRIGHTWELL<br>LAMPS &amp; BREEZES</div>
  <div class="abs rule" style="left:33px;top:232px;width:749px"></div>
  <div class="abs photo hero-photo" role="img" aria-label="Photo of a bright attic home office with a crystal chandelier"></div>

  <h1 class="abs title title-small">HOW ARE YOU</h1>
  <p class="abs title title-big">ENJOYING</p>
  <div class="abs tag">YOUR NEW LIGHTING?</div>
  <div class="abs rule" style="left:238px;top:1145px;width:338px"></div>
  <p class="abs intro">We hope you’re enjoying your recently installed lighting!</p>

  <section class="abs band-brown"></section>
  <section class="abs band-beige"></section>
  <section class="abs band-grey"></section>

  <p class="abs lead">Now that some time has passed, we wanted to check in and see how the lighting is working out for you. Your satisfaction is very important to us, and we’d love to hear your feedback on the following:</p>

  <div class="abs photo kitchen-photo" role="img" aria-label="Photo of a kitchen with open shelves and a table lamp"></div>
  <p class="abs question q1">Are you happy with the lighting in your space?</p>

  <p class="abs question q2">Was our service during the installation process satisfactory?</p>
  <div class="abs photo nook-photo" role="img" aria-label="Photo of a dining nook with a globe pendant light"></div>

  <div class="abs photo pendant-photo" role="img" aria-label="Photo of white pendant lights with gold interiors"></div>
  <p class="abs question q3">How was your experience with your Brightwell Lamps and Breezes representative?</p>

  <div class="abs foliage foliage-top" role="img" aria-label="Green foliage sprigs"></div>
  <div class="abs foliage-bottom" role="img" aria-label="Green foliage sprigs"></div>
  <p class="abs commit">We’re committed to providing the best possible service and are always looking for ways to improve.</p>
  <div class="abs rule" style="left:238px;top:3229px;width:338px"></div>
  <p class="abs help">If there’s anything we can do to assist further or if you have any concerns, please don’t hesitate to reach out.</p>

  <footer class="abs band-dark"></footer>
  <p class="abs thanks">Thank you once again for choosing Brightwell Lamps and Breezes. We look forward to hearing from you and hope to work with you again in the future!</p>
  <p class="abs regards">WARM REGARDS,</p>
  <p class="abs team">“Brightwell Lamps and Breezes Team”</p>
  <span class="abs social" style="left:372px" aria-label="Social link"></span>
  <span class="abs social" style="left:415px" aria-label="Social link"></span>
  <div class="abs rule-dark"></div>
  <p class="abs site">www.brightwelllamps.com</p>
</main>
</body>
</html>
```